Master Label Design for Velmora Botanic Products

Looking to update product labels and add consistency across our line with a new master label design. 'Velmora Botanic' has been a trusted name in the health marketplace providing quality herbal and dietary supplements since 1979. We have 8 products in need of a master label design, examples of our current labels are attached, and you can see more at our website, VelmoraBotanic.com. All 8 products currently have a 160mm x 58mm label size, while 3 products also have a 194mm x 68mm (Chaparral, Garlic Bright, and Bulvana Odorless Garlic).
Also, our logo is only prominent on the EDTA label, but that product is our #1 seller and most recognizable, it is at the artist's discretion what to do with our logo. (attached, if needed).
Please show me only the label designs for "EDTA".
Target Market(s)
-Health-conscious adults over 40 in North America who buy herbal and/or dietary supplements.
-->Cardiovascular health-conscious adults (a.k.a., "heart healthy" adults)
-->Adults with poor cardiovascular health seeking naturopathic/alternative options.
Industry/Entity Type
Health And Wellness
Logo Text
Velmora Botanic
Colors
Designer to choose colors to be used in the design.

```html
<!DOCTYPE html>
<html lang="en">
<head>
<meta charset="UTF-8">
<title>Velmora Botanic – Wild Bear's Garlic Label</title>
<link rel="stylesheet" href="https://fonts.googleapis.com/css2?family=Montserrat:wght@300;400;500;600&display=swap">
<style>
  :root {
    --backdrop: #a2a2a2;
    --label-blue: #00b2e5;
    --brush-teal: #0f8688;
    --gold: #d9a441;
    --gold-light: #f2c977;
    --brand-dark: #0b5f6a;
    --mark-maroon: #8a2c4c;
    --white: #ffffff;
  }
  * { margin: 0; padding: 0; box-sizing: border-box; }
  html, body {
    width: 1200px;
    height: 825px;
    overflow: hidden;
  }
  body {
    background: var(--backdrop);
    font-family: "Montserrat", sans-serif;
    position: relative;
  }
  .label {
    position: absolute;
    left: 50px;
    top: 192px;
    width: 1100px;
    height: 440px;
    background: var(--label-blue);
    overflow: hidden;
  }
  .brand-line {
    position: absolute;
    top: 34px;
    width: 100%;
    text-align: center;
    font-size: 13px;
    font-weight: 600;
    letter-spacing: 0.62em;
    color: var(--brand-dark);
  }
  .brush-stroke {
    position: absolute;
    left: 300px;
    top: 130px;
    width: 520px;
    height: 210px;
    border-radius: 46% 40% 44% 38% / 50% 42% 56% 46%;
    background: linear-gradient(100deg, #0c7d80 0%, var(--brush-teal) 45%, #12908f 100%);
    opacity: 0.96;
  }
  .hex-frame {
    position: absolute;
    left: 390px;
    top: 60px;
    width: 320px;
    height: 370px;
  }
  .maker-mark {
    position: absolute;
    top: 140px;
    width: 100%;
    display: flex;
    justify-content: center;
    align-items: center;
    gap: 8px;
  }
  .maker-mark__dot {
    width: 14px;
    height: 14px;
    border-radius: 50%;
    background: var(--mark-maroon);
  }
  .maker-mark__name {
    font-size: 17px;
    font-weight: 600;
    color: var(--mark-maroon);
    letter-spacing: 0.04em;
  }
  .product-name {
    position: absolute;
    top: 212px;
    width: 100%;
    text-align: center;
    font-size: 38px;
    font-weight: 300;
    color: var(--white);
    letter-spacing: 0.01em;
  }
  .organic-claim {
    position: absolute;
    top: 262px;
    width: 100%;
    text-align: center;
    font-size: 10px;
    font-weight: 400;
    color: var(--white);
    letter-spacing: 0.06em;
  }
  .divider {
    position: absolute;
    top: 286px;
    left: 470px;
    width: 160px;
    height: 1px;
    background: var(--white);
  }
  .benefits {
    position: absolute;
    top: 298px;
    width: 100%;
    text-align: center;
    font-size: 10px;
    line-height: 14px;
    font-weight: 400;
    color: var(--white);
    letter-spacing: 0.05em;
    list-style: none;
  }
  .count {
    position: absolute;
    top: 340px;
    width: 100%;
    text-align: center;
    color: var(--brand-dark);
  }
  .count__number {
    display: block;
    font-size: 22px;
    font-weight: 600;
    line-height: 22px;
  }
  .count__unit {
    display: block;
    font-size: 9px;
    font-weight: 500;
    letter-spacing: 0.05em;
  }
</style>
</head>
<body>
  <section class="label">
    <p class="brand-line">VELMORA BOTANIC</p>

    <div class="brush-stroke" role="img" aria-label="Painted teal brush stroke backdrop"></div>

    <svg class="hex-frame" viewBox="0 0 320 370" aria-hidden="true">
      <defs>
        <linearGradient id="goldLine" x1="0" y1="0" x2="1" y2="1">
          <stop offset="0" stop-color="#f2c977"/>
          <stop offset="0.5" stop-color="#d9a441"/>
          <stop offset="1" stop-color="#b9842e"/>
        </linearGradient>
      </defs>
      <polygon points="160,4 316,94 316,276 160,366 4,276 4,94"
               fill="none" stroke="url(#goldLine)" stroke-width="3"/>
    </svg>

    <div class="maker-mark">
      <span class="maker-mark__dot"></span>
      <span class="maker-mark__name">Velmora Botanic</span>
    </div>

    <h1 class="product-name">WILD BEAR'S GARLIC</h1>
    <p class="organic-claim">100% ORGANIC</p>
    <div class="divider"></div>
    <ul class="benefits">
      <li>ODORLESS</li>
      <li>ADENOSINE RICH</li>
    </ul>
    <p class="count">
      <span class="count__number">90</span>
      <span class="count__unit">CAPSULES</span>
    </p>
  </section>
</body>
</html>
```